Video Learning Web Application Site Design

We are a new company that produce and distribute educational videos using a subscription model on our website. The videos are streamed on our website and users can tailor their own course packages by creating playlists. Each video-lesson are also split into several smaller segments, and it should be easy to find and play those segments.

Please note that both the screenshots and wireframes provided are only how it looks right now, if you as the designer have a better idea on how to present it then please share it.
Updates

Please view the screenshots as well, I believe I forgot to include two buttons on the wireframes that should be on the Our Courses page. Also, there is no need to make a carbon copy of the wireframes/screenshots, I'd like you designers to come up with a better way of displaying the information if possible. For inspiration you can look at sites like ClipHarbor (I like the simplicity of their design) and to some extent the Tessel UI where they divide different areas of the page into clear "zones".

Thanks,

Project Deadline Extended
Reason: I have to extend the deadline because I've been really ill the last week. Will go through the current submissions now and provide feedback and looking forward to more submissions.

Target Market(s)

College and University students. Professionals wanting to expand their knowledge and people that want to learn new skills to get a promotion/new job.

Industry/Entity Type

Tailor

Requirements
Must have
• Must include the logo from the file "brainlark-logo".
• Should include two pages, one of the video-player page and one of the course list.
• Try to incorporate the colors from the logo.
• Please note: If you look at the video-player.png file just below "Åpne Tabell, lage..." there are two rows, those are sub-parts of the lesson. Both these and the main lesson itself must have some easy way to Play and Add to Playlist.
Nice to have
• We prefer flat design, with simple and clean icons. Don't overdo the colors, stay within 3-4 colors with variations of them.
Should not have
• 3D-like elements, lot of shadows or hard to ready text.

```html
<!DOCTYPE html>
<html lang="en">
<head>
<meta charset="utf-8">
<title>brainlark – Tabell 2013 Beginner</title>
<link href="https://fonts.googleapis.com/css2?family=Exo+2:wght@400;500;600&display=swap" rel="stylesheet">
<style>
:root{
  --blue:#1a7fb5;
  --blue-bright:#1b94d0;
  --blue-deep:#0e6594;
  --navy:#1d4a66;
  --sky:#a7d9ef;
  --sky-soft:#cfe8f4;
  --green:#8cc63f;
  --orange:#f39a1e;
  --red:#d8323d;
  --pink:#fbe3e4;
  --ink:#222;
  --mute:#8a8a8a;
  --dark:#161616;
  --dark-2:#1e1e1e;
  --line-dark:#2a2a2a;
  --panel:#f1f1f1;
  --line:#dedede;
}
*{box-sizing:border-box;margin:0;padding:0}
html,body{width:1200px;height:778px;overflow:hidden;background:#fff;font-family:"Exo 2",sans-serif;color:var(--ink)}
.app{position:relative;width:1200px;height:778px;overflow:hidden}

/* header */
.topbar{position:absolute;left:0;top:0;width:1200px;height:70px;background:#fff;border-bottom:3px solid var(--navy)}
.brand{position:absolute;left:16px;top:12px;display:flex;align-items:center;gap:8px}
.brand-dot{width:34px;height:34px;border-radius:50%;background:var(--blue)}
.brand-name{font-size:35px;font-weight:600;color:var(--blue);letter-spacing:.5px}
.session{position:absolute;right:74px;top:16px;display:flex;align-items:center;gap:8px;font-size:12px}
.btn-logout{background:var(--green);color:#fff;width:94px;height:18px;line-height:18px;text-align:center;font-size:12px}
.mainnav{position:absolute;left:629px;top:43px;width:497px;height:24px;background:var(--navy);display:flex;align-items:center}
.mainnav .menu{width:38px;height:24px;display:flex;align-items:center;justify-content:center;border-right:1px solid #2f6585}
.mainnav a{color:#fff;text-decoration:none;font-size:12px;font-weight:500;padding:0 14px;height:24px;line-height:24px;border-right:1px solid #2f6585}
.search{margin-left:9px;width:154px;height:17px;background:#fff}
.search-btn{width:24px;height:24px;background:var(--blue-bright);display:flex;align-items:center;justify-content:center;margin-left:auto}

/* sidebar */
.sidebar{position:absolute;left:0;top:70px;width:255px;height:708px;background:var(--dark);color:#cfcfcf}
.side-head{height:40px;line-height:40px;padding-left:10px;font-size:20px;color:#fff;border-bottom:1px solid var(--line-dark)}
.side-row{display:flex;align-items:center;border-bottom:1px solid var(--line-dark);font-size:13px}
.side-row .ico{width:40px;height:100%;display:flex;align-items:center;justify-content:center;border-right:1px solid var(--line-dark)}
.side-row .lbl{flex:1;padding-left:10px}
.side-row.muted{color:#6b6b6b}
.side-row.current{background:var(--blue-deep);color:#fff;border-color:var(--blue-deep)}
.side-row.current .ico{border-color:var(--blue-deep)}
.badge{min-width:24px;height:19px;line-height:19px;text-align:center;color:#fff;font-size:11px;margin-right:10px}
.badge.orange{background:var(--orange)}
.badge.green{background:var(--green)}
.course-sub{height:27px;display:flex;align-items:center;padding-left:43px;font-size:12px;color:#8a8a8a;background:#121d24;position:relative}
.course-sub .thumb{width:20px;height:20px;margin-right:8px}
.course-sub.active{background:var(--blue-bright);color:#fff;margin-left:40px;padding-left:3px}
.course-sub.active::after{content:"";position:absolute;right:0;top:7px;border:7px solid transparent;border-right-color:var(--panel)}

/* main */
.main{position:absolute;left:255px;top:70px;width:660px;height:708px;background:var(--panel)}
.video{position:absolute;left:19px;top:20px;width:628px;height:360px;background:#fff}
.video-frame{position:absolute;left:0;top:0;width:628px;height:327px;background:linear-gradient(135deg,#f7f7f7 0%,#e9d9cc 40%,#c9a98e 60%,#f2f2f2 100%)}
.controls{position:absolute;left:0;bottom:0;width:628px;height:33px;background:#000;display:flex;align-items:center;padding:0 10px;gap:10px;color:#fff;font-size:11px}
.progress{flex:1;height:4px;background:#1e4c66;position:relative}
.progress span{position:absolute;left:0;top:0;height:4px;width:43%;background:var(--blue-bright)}
.course-head{position:absolute;left:19px;top:393px;width:620px;height:71px;background:var(--dark-2);color:#fff}
.course-head .cover{position:absolute;left:0;top:0;width:71px;height:71px;background:linear-gradient(150deg,#dbe7ee,#7f98a8)}
.course-title{position:absolute;left:80px;top:4px;font-size:27px;font-weight:400}
.course-sub-text{position:absolute;left:82px;top:41px;font-size:11px;color:#9a9a9a;line-height:13px}
.btn-remove{position:absolute;right:0;top:8px;width:100px;height:22px;line-height:22px;text-align:center;background:var(--red);font-size:11px}
.btn-cues{position:absolute;left:393px;top:41px;width:118px;height:22px;line-height:22px;text-align:center;background:#555;font-size:11px}
.pager{position:absolute;right:0;top:41px;display:flex;height:22px;background:#333;font-size:11px;align-items:center}
.pager span{padding:0 8px}
.lessons{position:absolute;left:21px;top:477px;width:610px}
.lesson{display:flex;height:22px;border-bottom:1px solid var(--line);font-size:12px;align-items:center;background:#fff}
.lesson .cell{width:23px;height:21px;display:flex;align-items:center;justify-content:center}
.cell.add{background:var(--green)}
.cell.minus{background:#ea6b73}
.cell.star{background:#d9d9d9}
.cell.play{background:#e7e7e7}
.lesson .txt{padding-left:8px;color:#222}
.lesson.open{background:var(--pink)}
.lesson.child .txt{color:#1b5f8c}
.lesson.child .spacer{width:23px}
.lesson.playing{background:var(--sky-soft)}
.lesson.playing .star{background:var(--blue-deep)}
.lesson.playing .play{background:var(--blue-bright)}
.scroll{position:absolute;left:642px;top:477px;width:4px;height:231px;background:#ddd}
.scroll span{display:block;height:126px;background:#888}

/* right column */
.aside{position:absolute;left:925px;top:70px;width:210px;height:708px}
.explore{margin-top:22px;height:37px;background:var(--sky);display:flex;align-items:center;color:#fff;font-size:14px;font-weight:600}
.explore .menu{width:44px;display:flex;justify-content:center}
.explore span{padding-left:8px}
.aside h3{font-weight:400;font-size:16px;margin:10px 0 2px}
.aside h2{font-weight:400;font-size:19px;margin:16px 0 6px}
.ref{display:flex;align-items:center;border-bottom:1px solid #e6e6e6;font-size:12px;line-height:13px;min-height:21px}
.ref .cell{width:22px;align-self:stretch;display:flex;align-items:center;justify-content:center;background:#efefef}
.ref .cell+.cell{background:#f7f7f7}
.ref .txt{padding:2px 0 2px 10px;flex:1}
.ref.on{background:var(--sky-soft)}
.ref.on .cell{background:var(--blue-deep)}
.ref.on .cell+.cell{background:var(--blue-bright)}
.mini{display:flex;align-items:center;margin-bottom:8px;height:27px}
.mini .thumb{width:27px;height:27px;background:linear-gradient(150deg,#dfe9ef,#8aa1b0);margin-right:9px;flex:none}
.mini b{display:block;font-weight:400;font-size:14px;line-height:15px}
.mini small{display:block;font-size:9px;line-height:11px;color:var(--mute)}
</style>
</head>
<body>
<div class="app">

<header class="topbar">
  <div class="brand"><div class="brand-dot"></div><div class="brand-name">brainlark</div></div>
  <div class="session">Logged in as Quillmark <span class="btn-logout">Log Out</span></div>
  <nav class="mainnav">
    <div class="menu"><svg width="14" height="11"><path d="M0 1h14M0 5.5h14M0 10h14" stroke="#fff" stroke-width="2"/></svg></div>
    <a>About</a><a>Videos</a><a>Help</a><a>Options</a>
    <div class="search"></div>
    <div class="search-btn"><svg width="14" height="14"><circle cx="6" cy="6" r="4.5" fill="none" stroke="#fff" stroke-width="2"/><path d="M9 9l4 4" stroke="#fff" stroke-width="2"/></svg></div>
  </nav>
</header>

<aside class="sidebar">
  <div class="side-head">Introduction</div>
  <div class="side-row" style="height:39px"><div class="ico"><svg width="20" height="20"><circle cx="10" cy="10" r="8" fill="none" stroke="#666" stroke-width="2"/><path d="M7 7l6 0 0 6z" fill="#666"/></svg></div><div class="lbl">Introduction</div><span class="badge orange">12</span></div>
  <div class="side-head">Modules</div>
  <div class="side-row muted" style="height:37px"><div class="ico"><svg width="18" height="18"><rect x="1" y="6" width="10" height="10" fill="none" stroke="#666" stroke-width="2"/><path d="M7 2h9v9" fill="none" stroke="#666" stroke-width="2"/></svg></div><div class="lbl">Our Courses</div></div>
  <div class="side-row current" style="height:33px"><div class="ico"><svg width="18" height="18"><circle cx="9" cy="6" r="4" fill="none" stroke="#fff" stroke-width="2"/><path d="M2 17c0-5 14-5 14 0z" fill="none" stroke="#fff" stroke-width="2"/></svg></div><div class="lbl">Your Courses</div></div>
  <div class="course-sub"><span class="thumb" style="background:#e07b16"></span>OfficeDesk 2013 - Beginner</div>
  <div class="course-sub active"><span class="thumb" style="background:#9fb4c0"></span>Tabell 2013 - Beginner</div>
  <div class="course-sub"><span class="thumb" style="background:#0f2b45"></span>PixelForge 2013 - Beginner</div>
  <div class="course-sub"><span class="thumb" style="background:#3d6b3a"></span>Tabell 2013 - Advance</div>
  <div class="course-sub"><span class="thumb" style="background:#4a3b6b"></span>Tabell 2013 - Beginner</div>
  <div class="side-row" style="height:35px"><div class="ico"><svg width="18" height="18"><rect x="1" y="6" width="10" height="10" fill="none" stroke="#666" stroke-width="2"/><path d="M7 2h9v9" fill="none" stroke="#666" stroke-width="2"/></svg></div><div class="lbl">Lorem Courses</div></div>
  <div class="side-head">Playlists</div>
  <div class="side-row" style="height:34px"><div class="ico"><svg width="20" height="20"><circle cx="10" cy="10" r="8" fill="none" stroke="#555" stroke-width="2"/><path d="M8 6l5 4-5 4z" fill="#555"/></svg></div><div class="lbl">My Playlist 01</div><span class="badge orange">12</span></div>
  <div class="side-row" style="height:34px"><div class="ico"><svg width="20" height="20"><circle cx="10" cy="10" r="8" fill="none" stroke="#555" stroke-width="2"/><path d="M8 6l5 4-5 4z" fill="#555"/></svg></div><div class="lbl">Lorem Playlist</div><span class="badge green">4</span></div>
  <div class="side-row" style="height:34px"><div class="ico"><svg width="20" height="20"><circle cx="10" cy="10" r="8" fill="none" stroke="#555" stroke-width="2"/><path d="M8 6l5 4-5 4z" fill="#555"/></svg></div><div class="lbl">Impsum Plays</div></div>
  <div class="side-row" style="height:34px"><div class="ico"><svg width="20" height="20"><circle cx="10" cy="10" r="8" fill="none" stroke="#555" stroke-width="2"/><path d="M8 6l5 4-5 4z" fill="#555"/></svg></div><div class="lbl">PlayList Doner 02</div><span class="badge orange">3</span></div>
</aside>

<main class="main">
  <section class="video">
    <div class="video-frame" role="img" aria-label="Lesson video still: a group of smiling students holding notebooks"></div>
    <div class="controls">
      <svg width="14" height="14"><path d="M2 1l11 6-11 6z" fill="#fff"/></svg>
      <div class="progress"><span></span></div>
      <span>1:04/4:30</span>
      <svg width="18" height="14"><path d="M1 5h4l5-4v12l-5-4H1z" fill="#fff"/><path d="M12 4q3 3 0 6M14 2q5 5 0 10" stroke="#fff" fill="none" stroke-width="1.5"/></svg>
      <svg width="16" height="16"><path d="M1 5V1h4M11 1h4v4M15 11v4h-4M5 15H1v-4" stroke="#fff" fill="none" stroke-width="2"/></svg>
    </div>
  </section>

  <section class="course-head">
    <div class="cover" role="img" aria-label="Course cover artwork"></div>
    <h1 class="course-title">Tabell 2013 - Beginner</h1>
    <p class="course-sub-text">Lorem Impsum proin<br>Impsum Text</p>
    <div class="btn-remove">Remove Course</div>
    <div class="btn-cues">Show All Cues</div>
    <div class="pager"><span>◂</span><span style="background:#222;line-height:22px">1-10 of 50</span><span>▸</span></div>
  </section>

  <section class="lessons">
    <div class="lesson"><div class="cell add"><svg width="11" height="11"><path d="M5.5 0v11M0 5.5h11" stroke="#fff" stroke-width="2"/></svg></div><div class="cell star">★</div><div class="cell play">▸</div><div class="txt">Item 0 Lorem Impsum</div></div>
    <div class="lesson open"><div class="cell minus"><svg width="11" height="11"><path d="M0 5.5h11" stroke="#fff" stroke-width="2"/></svg></div><div class="cell star" style="background:#ef9aa0;color:#fff">★</div><div class="cell play">▸</div><div class="txt">Item 1</div></div>
    <div class="lesson child"><div class="spacer"></div><div class="cell star">★</div><div class="cell play">▸</div><div class="txt">Ipsum dolor sit amet, consectet 0</div></div>
    <div class="lesson child playing"><div class="spacer" style="background:var(--panel);height:21px"></div><div class="cell star" style="color:#fff">★</div><div class="cell play" style="color:#fff">▸</div><div class="txt">Lorem ipsum dolor sit amet, consectetur adipiscing Child 2</div></div>
    <div class="lesson child"><div class="spacer"></div><div class="cell star">★</div><div class="cell play">▸</div><div class="txt">Por sit amet, consectetur adipiscing Childas</div></div>
    <div class="lesson child"><div class="spacer"></div><div class="cell star">★</div><div class="cell play">▸</div><div class="txt">Dolor sit amet, consectetur adipiscing Child 43</div></div>
    <div class="lesson child"><div class="spacer"></div><div class="cell star">★</div><div class="cell play">▸</div><div class="txt">Amet, consectetur adipiscing Child 4</div></div>
    <div class="lesson"><div class="cell add"><svg width="11" height="11"><path d="M5.5 0v11M0 5.5h11" stroke="#fff" stroke-width="2"/></svg></div><div class="cell star">★</div><div class="cell play">▸</div><div class="txt">Item 0 Lorem Impsum</div></div>
    <div class="lesson"><div class="cell add"><svg width="11" height="11"><path d="M5.5 0v11M0 5.5h11" stroke="#fff" stroke-width="2"/></svg></div><div class="cell star">★</div><div class="cell play">▸</div><div class="txt">Item 0 Lorem Impsum</div></div>
    <div class="lesson"><div class="cell add"><svg width="11" height="11"><path d="M5.5 0v11M0 5.5h11" stroke="#fff" stroke-width="2"/></svg></div><div class="cell star">★</div><div class="cell play">▸</div><div class="txt">Item 0 Lorem Impsum</div></div>
  </section>
  <div class="scroll"><span></span></div>
</main>

<aside class="aside">
  <div class="explore"><div class="menu"><svg width="14" height="11"><path d="M0 1h14M0 5.5h14M0 10h14" stroke="#fff" stroke-width="2"/></svg></div><span>Explore Item 1</span></div>
  <h3>Downloads</h3>
  <div class="ref"><div class="cell">★</div><div class="cell">⤓</div><div class="txt">Download Lessons file (xls)</div></div>
  <div class="ref"><div class="cell">★</div><div class="cell">⤓</div><div class="txt">Download Study material sample (doc)</div></div>
  <h3>Cues</h3>
  <div class="ref"><div class="cell">★</div><div class="cell">▸</div><div class="txt">Ipsum dolor sit amet</div></div>
  <div class="ref on"><div class="cell" style="color:#fff">★</div><div class="cell" style="color:#fff">▸</div><div class="txt">Lorem ipsum dolor sit amet consectetur adipiscing</div></div>
  <div class="ref"><div class="cell">★</div><div class="cell">▸</div><div class="txt">Ipsum dolor sit amet</div></div>
  <div class="ref"><div class="cell">★</div><div class="cell">▸</div><div class="txt">Consectetur adipiscing 4</div></div>
  <div class="ref"><div class="cell">★</div><div class="cell">▸</div><div class="txt">Consectetur adipiscing Co-nsectetur adipiscing 4</div></div>
  <div class="ref"><div class="cell">★</div><div class="cell">▸</div><div class="txt">Consectetur adipiscing 4</div></div>
  <div class="ref"><div class="cell">★</div><div class="cell">▸</div><div class="txt">Consectetur adipiscing Co-nsectetur adipiscing 4</div></div>
  <div class="ref"><div class="cell">★</div><div class="cell">▸</div><div class="txt">Consectetur adipiscing 4</div></div>
  <h2>Related Courses</h2>
  <div class="mini"><div class="thumb" role="img" aria-label="Course thumbnail"></div><div><b>OfficeDesk Expert</b><small>June 2013</small></div></div>
  <div class="mini"><div class="thumb" role="img" aria-label="Course thumbnail"></div><div><b>PixelForge V3 Pro</b><small>August 2012</small></div></div>
  <div class="mini"><div class="thumb" role="img" aria-label="Course thumbnail"></div><div><b>Tabell Advance 2013</b><small>May 2013</small></div></div>
  <h2 style="margin-top:8px">Recently Viewed</h2>
  <div class="mini"><div class="thumb" role="img" aria-label="Course thumbnail"></div><div><b>Playlist Editor 2014</b><small>June 2013</small></div></div>
  <div class="mini"><div class="thumb" role="img" aria-label="Course thumbnail"></div><div><b>Script Coder Pro 12</b><small>September 1998</small></div></div>
  <div class="mini"><div class="thumb" role="img" aria-label="Course thumbnail"></div><div><b>MotionLab V3</b><small>May 2013</small></div></div>
</aside>

</div>
</body>
</html>
```